Advertising company unique advertising platform

we need a logo design for a new company based in Australia Melbourne. We develop innovated advertising platform where consumer can use this platform to get regular discount, as business owner they can use this platform for free advertisement. Payment for this advertisement platform only payable every two weeks, when I generate revenue for their business

Industry/Entity Type

Advertising

Contact Information for Business Card

Dale Morven | Co-Founder |Managing Director
Suite 718 240 Wattlebrook Lane Melbourne Vic 3000

ABN 38 614 207 923
Tel: +61 0487 259 318 | Email: dale.morven@plivorantu.com

Font styles to use
Decorative
Script

Requirements
Must have
• Try few different design and some round corner business card
Should not have
• One round corner business card...try 4 different colour background not only black, make sure two side is designed. Be creative so imagine you are giving this to a client make sure has wow factor, if you can also try one design with engrave like all the logo, words look 3d feel
• The word Advertising Platform use attached file font

```html
<!DOCTYPE html>
<html lang="en">
<head>
<meta charset="utf-8">
<title>Plivorantu – Business Card</title>
<link href="https://fonts.googleapis.com/css2?family=Open+Sans:wght@400;600;700&display=swap" rel="stylesheet">
<style>
  :root {
    --page-bg: #e9e6e3;
    --card-black: #141414;
    --card-black-edge: #0b0b0b;
    --emboss-text: #2a2a2a;
    --web-grey: #8d8d8d;
    --accent-orange: #f0582b;
    --accent-teal: #2fe0b2;
    --text-white: #f4f4f4;
    --divider: #9a9a9a;
  }
  * { margin: 0; padding: 0; box-sizing: border-box; }
  html, body {
    width: 1200px;
    height: 864px;
    overflow: hidden;
    background: var(--page-bg);
    font-family: "Open Sans", Arial, sans-serif;
  }
  .canvas {
    position: relative;
    width: 1200px;
    height: 864px;
  }
  .card {
    position: absolute;
    width: 540px;
    height: 310px;
    background: var(--card-black);
    border: 1px solid var(--card-black-edge);
    box-shadow: 0 10px 28px rgba(0,0,0,0.28);
  }

  /* Front side */
  .card-front { left: 50px; top: 150px; }
  .front-mark {
    position: absolute;
    left: 0; right: 0; top: 92px;
    display: flex;
    justify-content: center;
    align-items: center;
    gap: 12px;
  }
  .front-mark .mark-dot {
    width: 34px; height: 34px;
    border-radius: 50%;
    background: var(--emboss-text);
  }
  .front-mark .mark-name {
    font-weight: 600;
    font-size: 34px;
    color: var(--emboss-text);
  }
  .front-web {
    position: absolute;
    left: 0; right: 0; top: 196px;
    text-align: center;
    font-size: 14px;
    letter-spacing: 5px;
    color: var(--web-grey);
  }

  /* Back side */
  .card-back { left: 610px; top: 400px; }
  .brand-lockup {
    position: absolute;
    left: 26px; top: 126px;
    display: flex;
    align-items: center;
    gap: 10px;
  }
  .brand-lockup .brand-dot {
    width: 30px; height: 30px;
    border-radius: 50%;
    background: var(--accent-orange);
  }
  .brand-lockup .brand-name {
    font-weight: 700;
    font-size: 27px;
    color: var(--accent-orange);
  }
  .divider {
    position: absolute;
    left: 232px; top: 40px;
    width: 2px; height: 230px;
    background: linear-gradient(to bottom, transparent, var(--divider) 30%, var(--divider) 70%, transparent);
  }
  .contact {
    position: absolute;
    left: 250px; top: 44px;
    font-size: 14px;
    line-height: 19px;
    color: var(--text-white);
  }
  .contact .person-name {
    font-weight: 700;
    color: var(--accent-orange);
    text-transform: uppercase;
  }
  .contact .person-role {
    color: var(--accent-teal);
    text-transform: uppercase;
    font-size: 15px;
    line-height: 19px;
  }
  .contact .address { margin-top: 6px; }
  .contact .reach-line {
    display: flex;
    align-items: center;
    gap: 7px;
  }
  .contact .reach-line svg { width: 11px; height: 11px; flex: none; }
  .contact .reach { margin-top: 2px; }
</style>
</head>
<body>
<main class="canvas">
  <section class="card card-front" aria-label="Card front">
    <div class="front-mark">
      <span class="mark-dot"></span>
      <span class="mark-name">Kestrel Hub</span>
    </div>
    <p class="front-web">www.plivorantu.com</p>
  </section>

  <section class="card card-back" aria-label="Card back">
    <div class="brand-lockup">
      <span class="brand-dot"></span>
      <span class="brand-name">Kestrel Hub</span>
    </div>
    <div class="divider"></div>
    <div class="contact">
      <p class="person-name">Dale Morven</p>
      <p class="person-role">Co-Founder</p>
      <p class="person-role">Managing Director</p>
      <div class="address">
        <p>Plivorantu</p>
        <p>ABN 38 614 207 923</p>
        <p>Suite 718 240 Wattlebrook Lane</p>
        <p>Melbourne Vic 3000</p>
      </div>
      <div class="reach">
        <p class="reach-line">
          <svg viewBox="0 0 12 12" aria-hidden="true"><path d="M2 1h2.5l1 2.6-1.4 1a6 6 0 0 0 3.3 3.3l1-1.4 2.6 1V10a1 1 0 0 1-1 1A9 9 0 0 1 1 2a1 1 0 0 1 1-1z" fill="#f0582b"/></svg>
          <span>+61 0487 259 318</span>
        </p>
        <p class="reach-line">
          <svg viewBox="0 0 12 12" aria-hidden="true"><rect x="0.5" y="2" width="11" height="8" rx="1" fill="#f0582b"/><path d="M1 2.6 6 6.5l5-3.9" fill="none" stroke="#141414" stroke-width="1"/></svg>
          <span>dale.morven@plivorantu.com</span>
        </p>
      </div>
    </div>
  </section>
</main>
</body>
</html>
```